Dalvick's Business Card

I need some designs for a new business card including the new logo attached. An old example of our business card is also attached to show all the data that should be included on the new design.
**I added some more examples someone had mocked up**

Contact Information for Business Card

Should include all info on other examples uploaded.

```html
<!DOCTYPE html>
<html lang="en">
<head>
<meta charset="utf-8">
<title>Dalvick's Business Card</title>
<link href="https://fonts.googleapis.com/css2?family=Montserrat:wght@500;600;700;800&display=swap" rel="stylesheet">
<style>
  :root {
    --stage: #d6d6d6;
    --card: #000000;
    --blue: #0a74c4;
    --red: #ec1c24;
    --rule: #3a3a3a;
    --font: 'Montserrat', Arial, sans-serif;
  }
  * { margin: 0; padding: 0; box-sizing: border-box; }
  html, body { width: 1200px; height: 900px; overflow: hidden; }
  body { background: var(--stage); font-family: var(--font); position: relative; }

  .card {
    position: absolute;
    width: 600px;
    height: 343px;
    background: var(--card);
    border-radius: 30px;
    box-shadow: 0 10px 24px rgba(0,0,0,.28);
    overflow: hidden;
  }
  .card--front { left: 70px; top: 80px; }
  .card--back { left: 530px; top: 477px; }

  /* Front */
  .brand {
    position: absolute; left: 0; right: 0; top: 70px;
    display: flex; flex-direction: column; align-items: center;
  }
  .brand__row { display: flex; align-items: center; gap: 16px; }
  .brand__dot { width: 30px; height: 30px; border-radius: 50%; background: var(--red); }
  .brand__name {
    font-weight: 700; font-size: 62px; letter-spacing: 2px;
    color: var(--blue); line-height: 1;
  }
  .brand__tagline {
    margin-top: 6px; margin-left: 46px;
    font-weight: 600; font-size: 14.5px; letter-spacing: 1.2px;
    color: var(--red); text-transform: uppercase;
  }
  .front__area {
    position: absolute; left: 0; right: 0; top: 190px;
    text-align: center; color: var(--blue);
    font-weight: 500; font-size: 18px; letter-spacing: .5px;
  }
  .front__cta {
    position: absolute; left: 0; right: 0; top: 230px;
    text-align: center; color: var(--red);
    font-weight: 800; font-size: 19px; line-height: 1.25;
    letter-spacing: .6px; text-transform: uppercase;
  }

  /* Back */
  .back__stripe {
    position: absolute; left: 0; top: 120px; width: 30px; height: 44px;
    display: flex;
  }
  .back__stripe span { flex: 1; }
  .back__stripe .stripe-red { background: var(--red); }
  .back__stripe .stripe-blue { background: var(--blue); }
  .back__person {
    position: absolute; left: 58px; top: 124px;
    font-weight: 800; font-size: 26px; letter-spacing: 1.5px;
    text-transform: uppercase;
  }
  .back__person .first { color: var(--red); }
  .back__person .last { color: var(--blue); }

  .contact { position: absolute; left: 130px; top: 218px; list-style: none; }
  .contact__item {
    display: flex; align-items: center; gap: 10px;
    font-weight: 500; font-size: 17px; line-height: 24px;
  }
  .contact__item svg { width: 18px; height: 18px; flex: none; }
  .contact__item--phone { color: var(--red); }
  .contact__item--email { color: var(--blue); }
  .contact__rule { width: 190px; height: 1px; background: var(--rule); margin: 8px 0 8px 4px; }
  .credentials {
    position: absolute; left: 134px; top: 285px;
    font-weight: 800; font-size: 17px; line-height: 1.2;
    letter-spacing: .8px; text-transform: uppercase;
  }
  .credentials .licensed { color: var(--blue); }
  .credentials .family { color: var(--red); }

  .back__mark {
    position: absolute; right: 34px; top: 70px;
    display: flex; align-items: center; gap: 12px;
  }
  .back__mark-dot { width: 26px; height: 26px; border-radius: 50%; background: var(--red); }
  .back__mark-name {
    font-weight: 700; font-size: 44px; letter-spacing: 1.5px;
    color: var(--blue); line-height: 1;
  }
</style>
</head>
<body>

  <section class="card card--front" aria-label="Business card front">
    <div class="brand">
      <div class="brand__row">
        <span class="brand__dot"></span>
        <span class="brand__name">DALVICK'S</span>
      </div>
      <div class="brand__tagline">Air Conditioning &amp; Heating Service</div>
    </div>
    <p class="front__area">Serves Millbrook, IA &amp; Surrounding Areas</p>
    <p class="front__cta">Call today for all your HVAC,<br>Refrigeration &amp; Plumbing Needs</p>
  </section>

  <section class="card card--back" aria-label="Business card back">
    <div class="back__mark">
      <span class="back__mark-dot"></span>
      <span class="back__mark-name">DALVICK'S</span>
    </div>

    <div class="back__stripe"><span class="stripe-red"></span><span class="stripe-blue"></span></div>
    <h1 class="back__person"><span class="first">Mark</span> <span class="last">Dalvick</span></h1>

    <ul class="contact">
      <li class="contact__item contact__item--phone">
        <svg viewBox="0 0 24 24" aria-hidden="true"><path fill="var(--blue)" d="M6.6 10.8a15.1 15.1 0 0 0 6.6 6.6l2.2-2.2c.3-.3.7-.4 1-.2 1.1.4 2.3.6 3.6.6.6 0 1 .4 1 1V20c0 .6-.4 1-1 1C10.6 21 3 13.4 3 4c0-.6.4-1 1-1h3.5c.6 0 1 .4 1 1 0 1.3.2 2.5.6 3.6.1.3 0 .7-.2 1l-2.3 2.2z"/></svg>
        555.014.2290
      </li>
      <li class="contact__item contact__item--email">
        <svg viewBox="0 0 24 24" aria-hidden="true"><path fill="var(--blue)" d="M3 5h18c.6 0 1 .4 1 1v12c0 .6-.4 1-1 1H3c-.6 0-1-.4-1-1V6c0-.6.4-1 1-1zm9 7.5L4 7.2V8l8 5.3L20 8v-.8l-8 5.3z"/></svg>
        hvacdalvick@mailbox.com
      </li>
    </ul>
    <div class="contact__rule" style="position:absolute;left:130px;top:276px;margin:0;"></div>

    <p class="credentials">
      <span class="licensed">Licensed &amp; Insured</span><br>
      <span class="family">Family Owned &amp; Operated</span>
    </p>
  </section>

</body>
</html>
```